RW Holloway LLC Business Card - Civil Engineering & Consulting Firm

We need a Business Card that is elegant, and masculine.  It is our Professional Civil Engineering & Consulting Company located in San Antonio TX (Not s construction or builder firm- no gears & no tool images please). We provide civil engineering services including  commercial site plans, grading and drainage plans, utility plans, hydraulics and hydrology, land planning, utility coordination, and other general civil engineering services related to commercial and residential development.
We have 2 existing Logos. We would like to convey reliability, strength, trustworthiness and attention to detail.  Blues and orange tones as per logo We are OK with the use of a darker blue in the mix.  We have 2 logo versions - Full Company Name Logo to go on the back of card, & Small Icon Logo for the front w/ personal Info.

Target Market(s)
Architects, Real Estate Developers, Other Strctural Engineers, Surveyers, General Contractors
Industry/Entity Type
Professional Civil Engineering
Contact Information for Business Card
Name, Position, Address, Cell & Office #, email, and company website
Font styles to use
Other font styles liked:
- Avian
Requirements
Should not have
- No Tools, No Gears, no Cranes, or Construction Equipment.

```html
<!DOCTYPE html>
<html lang="en">
<head>
<meta charset="utf-8">
<title>RW Holloway LLC – Business Card</title>
<link href="https://fonts.googleapis.com/css2?family=Lato:wght@400;700&display=swap" rel="stylesheet">
<style>
  :root {
    --backdrop: #2b2b2d;
    --card: #1d1f22;
    --blue: #6fa8dc;
    --orange: #f7941d;
    --white: #f2f2f2;
    --rule: #7a7c80;
  }
  html, body {
    margin: 0;
    padding: 0;
    width: 1200px;
    height: 1108px;
    overflow: hidden;
    background: var(--backdrop);
    font-family: "Lato", sans-serif;
  }
  .canvas {
    position: relative;
    width: 1200px;
    height: 1108px;
  }
  .card {
    position: absolute;
    top: 170px;
    width: 420px;
    height: 680px;
    border-radius: 22px;
    background: var(--card);
    box-shadow: 0 18px 40px rgba(0,0,0,0.45);
    overflow: hidden;
  }
  .card--front { left: 140px; }
  .card--back { left: 640px; }

  .front__brand {
    position: absolute;
    top: 150px;
    left: 0;
    right: 0;
    text-align: center;
    color: var(--blue);
    font-size: 36px;
    font-weight: 400;
    letter-spacing: 2px;
  }
  .person {
    position: absolute;
    top: 330px;
    left: 0;
    right: 0;
    text-align: center;
  }
  .person__name {
    margin: 0;
    font-size: 30px;
    font-weight: 400;
    letter-spacing: 0.5px;
    color: var(--blue);
  }
  .person__name .surname { color: var(--orange); font-weight: 700; }
  .person__role {
    margin: 4px 0 0;
    font-size: 20px;
    color: var(--white);
  }
  .contact-icons {
    position: absolute;
    top: 428px;
    left: 50px;
    right: 50px;
    display: flex;
    align-items: center;
    gap: 10px;
  }
  .contact-icons .rule { flex: 1; height: 1px; background: var(--rule); }
  .contact-icons svg { display: block; }
  .contact {
    position: absolute;
    top: 488px;
    left: 0;
    right: 0;
    text-align: center;
    color: var(--white);
    font-size: 20px;
    line-height: 30px;
  }
  .contact p { margin: 0; }
  .contact .divider {
    width: 320px;
    height: 1px;
    margin: 12px auto;
    background: var(--rule);
  }

  .back__pattern {
    position: absolute;
    inset: 0;
    background: linear-gradient(160deg, #4a4c50 0%, #2a2c30 45%, #16181a 100%);
  }
  .back__brand {
    position: absolute;
    top: 500px;
    left: 0;
    right: 0;
    text-align: center;
    color: var(--orange);
    font-size: 26px;
    font-weight: 400;
    letter-spacing: 1px;
  }
</style>
</head>
<body>
<main class="canvas">
  <section class="card card--front" aria-label="Card front">
    <div class="front__brand">RW Holloway LLC</div>

    <div class="person">
      <h1 class="person__name">DANIEL <span class="surname">REYES</span></h1>
      <p class="person__role">Managing Director</p>
    </div>

    <div class="contact-icons">
      <span class="rule"></span>
      <svg width="34" height="34" viewBox="0 0 34 34" aria-label="Phone">
        <rect width="34" height="34" rx="6" fill="var(--blue)"/>
        <path d="M11 9c2 0 3 3 3 4s-2 1-2 2c0 2 3 5 5 5 1 0 1-2 2-2s4 1 4 3-2 3-3 3c-6 0-12-6-12-12 0-1 1-3 3-3z" fill="var(--card)"/>
      </svg>
      <svg width="34" height="34" viewBox="0 0 34 34" aria-label="Email">
        <rect width="34" height="34" rx="6" fill="var(--blue)"/>
        <rect x="8" y="11" width="18" height="12" fill="none" stroke="var(--card)" stroke-width="2"/>
        <path d="M8 11l9 7 9-7M8 23l7-6M26 23l-7-6" fill="none" stroke="var(--card)" stroke-width="1.6"/>
      </svg>
      <svg width="34" height="34" viewBox="0 0 34 34" aria-label="Website">
        <rect width="34" height="34" rx="6" fill="var(--blue)"/>
        <circle cx="17" cy="17" r="9" fill="none" stroke="var(--card)" stroke-width="2"/>
        <ellipse cx="17" cy="17" rx="4" ry="9" fill="none" stroke="var(--card)" stroke-width="1.5"/>
        <path d="M8 17h18" stroke="var(--card)" stroke-width="1.5"/>
      </svg>
      <span class="rule"></span>
    </div>

    <div class="contact">
      <p>044-555 010 200</p>
      <p>info@rwholloway.com</p>
      <p>www.rwholloway.com</p>
      <div class="divider"></div>
      <p>421, Mission Ridge Road</p>
      <p>78205, San Antonio TX</p>
    </div>
  </section>

  <section class="card card--back" aria-label="Card back">
    <div class="back__pattern" role="img" aria-label="Repeated faint brand monogram pattern fading from grey to black"></div>
    <div class="back__brand">RW Holloway LLC</div>
  </section>
</main>
</body>
</html>
```